Personal Injury Lawyer Billboard

I would like a design created featuring the image of the lawyer centered in the middle of the design.
To the left of the lawyer's image it should read "INJURED?"
To the right of the lawyer's image, it should read "CALL DEAN!"
Under Call Dean, include the phone number 318-555-0187.
At the bottom of the design include the lawyers information "Dean Marlowe Accident & Injury Lawyers"
PLEASE REMOVED THE BACKGROUND IMAGERY OF THE PHOTO SUBMITTED. Also, the colors for this design should match the colors shown in the logo (navy, white and relective soft gold). Please use those color combinations in ways that best stand out.

```html
<!DOCTYPE html>
<html lang="en">
<head>
<meta charset="utf-8">
<title>Dean Marlowe Accident &amp; Injury Lawyers – Billboard</title>
<link rel="stylesheet" href="https://fonts.googleapis.com/css2?family=Bebas+Neue&family=Outfit:wght@600&display=swap">
<style>
  :root {
    --navy: #0a1f4a;
    --navy-grid: rgba(90, 120, 170, 0.14);
    --gold: #bea673;
    --white: #ffffff;
    --photo-top: #2a3f6e;
    --photo-bottom: #141d3a;
  }
  * { margin: 0; padding: 0; box-sizing: border-box; }
  html, body { width: 1200px; height: 800px; overflow: hidden; background: var(--navy); }
  .billboard {
    position: relative;
    width: 1200px;
    height: 800px;
    overflow: hidden;
    background-color: var(--navy);
    background-image:
      repeating-linear-gradient(90deg, var(--navy-grid) 0 1px, transparent 1px 57px),
      repeating-linear-gradient(0deg, var(--navy-grid) 0 1px, transparent 1px 57px);
    font-family: "Bebas Neue", "Arial Narrow", sans-serif;
    font-weight: 400;
  }
  .headline {
    position: absolute;
    text-transform: uppercase;
    font-weight: 400;
    white-space: nowrap;
  }
  .headline--question {
    left: 68px;
    top: 165px;
    font-size: 133px;
    line-height: 1;
    color: var(--gold);
  }
  .headline--call {
    left: 806px;
    width: 320px;
    top: 70px;
    font-size: 130px;
    line-height: 127px;
    text-align: center;
    color: var(--white);
  }
  .phone {
    position: absolute;
    left: 806px;
    width: 320px;
    top: 327px;
    text-align: center;
    font-family: "Outfit", Arial, sans-serif;
    font-weight: 600;
    font-size: 48px;
    line-height: 1;
    letter-spacing: -0.5px;
    color: var(--gold);
    white-space: nowrap;
  }
  .lawyer-photo {
    position: absolute;
    left: 402px;
    top: 57px;
    width: 382px;
    height: 523px;
    background: linear-gradient(180deg, var(--photo-top), var(--photo-bottom));
    clip-path: polygon(100px 0, 230px 0, 242px 230px, 350px 250px, 382px 523px, 0 523px, 20px 250px, 88px 230px);
  }
  .divider {
    position: absolute;
    left: 0;
    top: 580px;
    width: 1200px;
    height: 6px;
    background: var(--gold);
  }
  .firm-name {
    position: absolute;
    left: 0;
    width: 1200px;
    text-align: center;
    color: var(--white);
    line-height: 1;
    text-transform: uppercase;
    white-space: nowrap;
  }
  .firm-name--primary { top: 620px; font-size: 87px; letter-spacing: 1px; }
  .firm-name--secondary { top: 712px; font-size: 49px; letter-spacing: 1px; }
</style>
</head>
<body>
  <main class="billboard">
    <h1 class="headline headline--question">Injured?</h1>

    <div class="lawyer-photo" role="img" aria-label="Cut-out photo of attorney Dean Marlowe smiling in a navy suit and green tie, raising a fist"></div>

    <h2 class="headline headline--call">Call<br>Dean!</h2>
    <p class="phone">318-555-0187</p>

    <div class="divider"></div>

    <p class="firm-name firm-name--primary">Dean Marlowe</p>
    <p class="firm-name firm-name--secondary">Accident &amp; Injury Lawyers</p>
  </main>
</body>
</html>
```